VelkaVision.com

Complete Website Design (Godaddy) and company Branding / Logo Design. The products will sell are only done in-person and are installed. So this site does not need to be an e-commerce site. We will only be giving out information and collecting customer inquires. Website will only need to be about 3 to 5 pages.

```html
<!DOCTYPE html>
<html lang="en">
<head>
<meta charset="UTF-8">
<title>Velka Vision</title>
<link href="https://fonts.googleapis.com/css2?family=Poppins:wght@500;600&family=Lato:wght@400;700&display=swap" rel="stylesheet">
<style>
  :root {
    --brand-blue: #2aabf0;
    --ink: #0b0b0b;
    --text: #222;
    --field-border: #5aaee6;
    --hero-bg: #eceeef;
    --white: #ffffff;
  }
  * { box-sizing: border-box; margin: 0; padding: 0; }
  html, body { width: 1191px; height: 1200px; overflow: hidden; background: var(--white); }
  body { position: relative; font-family: "Lato", sans-serif; color: var(--text); }

  .site-header { position: absolute; left: 0; top: 0; width: 1191px; height: 94px; background: var(--white); z-index: 3; }
  .brand { position: absolute; left: 110px; top: 27px; font-family: "Poppins", sans-serif; font-weight: 600; font-size: 26px; color: var(--ink); }
  .menu-icon { position: absolute; left: 884px; top: 36px; }
  .btn {
    position: absolute; display: flex; align-items: center; justify-content: center;
    background: var(--brand-blue); color: var(--ink); border-radius: 30px;
    font-family: "Poppins", sans-serif; font-weight: 500; font-size: 15px;
  }
  .btn-contact { left: 950px; top: 26px; width: 130px; height: 43px; }

  .hero { position: absolute; left: 0; top: 94px; width: 1191px; height: 500px; background: linear-gradient(90deg, #eef0f1 0%, #e9ebec 45%, #e4e6e8 100%); }
  .hero-photo {
    position: absolute; left: 460px; top: 0; width: 731px; height: 500px;
    background: linear-gradient(90deg, rgba(233,235,236,0) 0%, #d9dbdd 18%, #bfc2c5 45%, #a9acaf 70%, #cfd1d3 100%);
  }
  .hero-copy { position: absolute; left: 110px; top: 104px; width: 360px; }
  .hero-kicker { font-family: "Poppins", sans-serif; font-weight: 500; font-size: 20px; color: var(--ink); }
  .hero-title { font-family: "Poppins", sans-serif; font-weight: 500; font-size: 49px; line-height: 1.2; color: var(--ink); margin-top: 4px; }
  .hero-text { font-size: 13.6px; line-height: 25.5px; color: var(--text); margin-top: 6px; width: 350px; }
  .btn-start { left: 109px; top: 392px; width: 149px; height: 51px; font-size: 15.5px; }

  .contact-card { position: absolute; left: 111px; top: 519px; width: 970px; height: 560px; background: var(--white); border-radius: 34px 34px 0 0; z-index: 2; }
  .contact-title { position: absolute; left: 0; top: 552px; width: 1191px; text-align: center; font-family: "Poppins", sans-serif; font-weight: 500; font-size: 39px; color: var(--ink); z-index: 3; }
  .field {
    position: absolute; border: 1px solid var(--field-border); border-radius: 2px; background: var(--white);
    padding: 0 23px; display: flex; align-items: center;
    font-weight: 700; font-size: 14px; color: #333; z-index: 3;
  }
  .field-half { width: 441px; height: 64px; }
  .field-message { left: 137px; top: 789px; width: 919px; height: 150px; align-items: flex-start; padding-top: 24px; }
  .btn-submit { left: 521px; top: 981px; width: 149px; height: 50px; font-size: 15.5px; z-index: 3; }

  .site-footer { position: absolute; left: 0; top: 1103px; width: 1191px; height: 97px; background: var(--brand-blue); display: flex; align-items: center; justify-content: center; }
  .site-footer p { font-family: "Poppins", sans-serif; font-weight: 600; font-size: 18px; color: var(--white); }
</style>
</head>
<body>
  <header class="site-header">
    <div class="brand">Velka Vision</div>
    <svg class="menu-icon" width="30" height="24" viewBox="0 0 30 24" aria-hidden="true">
      <rect x="6" y="1" width="22" height="3" rx="1.5" fill="#111"/>
      <rect x="0" y="10" width="28" height="3" rx="1.5" fill="#111"/>
      <rect x="12" y="19" width="16" height="3" rx="1.5" fill="#111"/>
    </svg>
    <a class="btn btn-contact">Contact Us</a>
  </header>

  <section class="hero">
    <div class="hero-photo" role="img" aria-label="Photo of two installers mounting a large flat-screen TV on a white wall between speakers"></div>
    <div class="hero-copy">
      <p class="hero-kicker">Welcome to</p>
      <h1 class="hero-title">Velka Vision</h1>
      <p class="hero-text">Itaque earum rerum hic tenetur a sapiente delectus, ut aut reiciendis voluptatibus maiores alias consequatur aut perferendis doloribus asperiores repellat.</p>
    </div>
  </section>
  <a class="btn btn-start" style="z-index:3">Get Started</a>

  <div class="contact-card"></div>
  <h2 class="contact-title">Contact Form</h2>
  <div class="field field-half" style="left:137px;top:626px">Name</div>
  <div class="field field-half" style="left:613px;top:626px">Email</div>
  <div class="field field-half" style="left:137px;top:708px">Phone Number</div>
  <div class="field field-half" style="left:613px;top:708px">Address</div>
  <div class="field field-message">Message</div>
  <a class="btn btn-submit">Submit</a>

  <footer class="site-footer">
    <p>Copyrights@2024.VelkaVision.All Rights Reserved</p>
  </footer>
</body>
</html>
```